Vantro cards

I am in the auto motive, transportation business I would like a business card that is Something cool, modern edgy, having to do with car culture. I offer towing service for high and exotic cars. I also provide towing for collisions and car accidents. I offer open and enclosed transport nationwide.

Target Market(s)

Car culture people high end auto collectors

Industry/Entity Type

Towing car carrier

Contact Information for Business Card

My company colors black yellow and silver

Font styles to use
Serif

```html
<!DOCTYPE html>
<html lang="en">
<head>
<meta charset="utf-8">
<title>Vantro Transportation – Business Cards</title>
<link rel="stylesheet" href="https://fonts.googleapis.com/css2?family=Arvo:wght@400&family=Lato:wght@400;900&display=swap">
<style>
  :root {
    --page-bg: #3a3a3c;
    --card-white: #ffffff;
    --card-black: #1f1f1f;
    --brand-yellow: #f6d94a;
    --ink: #111111;
    --ink-soft: #222222;
  }
  * { box-sizing: border-box; margin: 0; padding: 0; }
  html, body {
    width: 1200px; height: 800px; overflow: hidden;
    background: var(--page-bg);
  }
  .sheet {
    width: 1200px; height: 800px;
    display: flex; flex-direction: column;
    align-items: center; justify-content: center; gap: 56px;
  }
  .card {
    width: 560px; height: 320px;
    border-radius: 22px;
    position: relative;
    overflow: hidden;
    box-shadow: 0 4px 0 var(--brand-yellow), 0 14px 30px rgba(0,0,0,.45);
  }
  .card--front { background: var(--card-white); }
  .card--back {
    background: var(--card-black);
    display: flex; align-items: center; justify-content: center;
  }

  .brand-mark {
    font-family: "Lato", sans-serif;
    font-weight: 900;
    text-transform: uppercase;
    color: var(--ink);
    display: flex; flex-direction: column; align-items: center;
    line-height: 1;
    text-align: center;
  }
  .brand-mark__name { font-size: 50px; letter-spacing: 2px; }
  .brand-mark__sub { font-size: 14px; letter-spacing: 3px; margin-top: 8px; }
  .brand-mark__square {
    width: 18px; height: 18px; background: var(--brand-yellow); margin-bottom: 12px;
  }
  .card--back .brand-mark { color: var(--card-white); }
  .card--back .brand-mark__name { font-size: 64px; }
  .card--back .brand-mark__sub { font-size: 18px; letter-spacing: 4px; }

  .front__logo {
    position: absolute; left: 0; top: 0; width: 246px; height: 100%;
    display: flex; align-items: center; justify-content: center;
  }
  .front__divider {
    position: absolute; left: 254px; top: 60px;
    width: 3px; height: 200px; background: var(--brand-yellow);
  }
  .front__details {
    position: absolute; left: 286px; top: 48px; right: 24px;
    font-family: "Lato", sans-serif; color: var(--ink-soft);
  }
  .person__name {
    font-family: "Arvo", serif; font-size: 24px; letter-spacing: 1px;
    text-transform: uppercase; color: var(--ink);
  }
  .person__title { font-size: 14px; margin-top: 2px; }
  .contact { list-style: none; margin-top: 14px; font-size: 13.5px; }
  .contact__item { display: flex; align-items: flex-start; gap: 10px; line-height: 1.45; }
  .contact__item + .contact__item { margin-top: 2px; }
  .contact__item--address { margin-bottom: 8px; }
  .contact__icon { width: 12px; height: 12px; flex: none; margin-top: 4px; fill: var(--ink); }
</style>
</head>
<body>
<main class="sheet">
  <section class="card card--front" aria-label="Business card front">
    <div class="front__logo">
      <div class="brand-mark">
        <span class="brand-mark__square"></span>
        <span class="brand-mark__name">Vantro</span>
        <span class="brand-mark__sub">Transportation</span>
      </div>
    </div>
    <div class="front__divider"></div>
    <div class="front__details">
      <h1 class="person__name">Daniel Brooks</h1>
      <p class="person__title">Managing Director</p>
      <ul class="contact">
        <li class="contact__item contact__item--address">
          <svg class="contact__icon" viewBox="0 0 12 12"><path d="M6 0a4 4 0 0 0-4 4c0 3 4 8 4 8s4-5 4-8a4 4 0 0 0-4-4zm0 5.6A1.6 1.6 0 1 1 6 2.4a1.6 1.6 0 0 1 0 3.2z"/></svg>
          <span>Your Address, City<br>State, Zip 1235</span>
        </li>
        <li class="contact__item">
          <svg class="contact__icon" viewBox="0 0 12 12"><path d="M2.5 0.5l2 2.2-1 1.3c.8 1.6 2 2.8 3.6 3.6l1.3-1 2.2 2-1.3 2.1C4.8 10.5 1.5 7.2.4 1.8z"/></svg>
          <span>123-456-7890</span>
        </li>
        <li class="contact__item">
          <svg class="contact__icon" viewBox="0 0 12 12"><path d="M3 0h6a1 1 0 0 1 1 1v10a1 1 0 0 1-1 1H3a1 1 0 0 1-1-1V1a1 1 0 0 1 1-1zm.6 1.4v8h4.8v-8z"/></svg>
          <span>123-456-7890</span>
        </li>
        <li class="contact__item">
          <svg class="contact__icon" viewBox="0 0 12 12"><path d="M3 0h5v3H3zM1 4h10v6H9v2H3v-2H1zm3 4v3h4V8z"/></svg>
          <span>123-456-7890</span>
        </li>
        <li class="contact__item">
          <svg class="contact__icon" viewBox="0 0 12 12"><path d="M0 2h12v8H0zm1 1v.4l5 3.3 5-3.3V3z"/></svg>
          <span>brooks@yourwebsite.com</span>
        </li>
        <li class="contact__item">
          <svg class="contact__icon" viewBox="0 0 12 12"><path d="M6 0a6 6 0 1 0 0 12A6 6 0 0 0 6 0zm0 1.2c.7.8 1.2 2 1.4 3.3H4.6C4.8 3.2 5.3 2 6 1.2zM1.3 5.5h2.3c0 .4 0 .7.1 1H1.3zm3.3 1h2.8c-.2 1.5-.7 2.6-1.4 3.4-.7-.8-1.2-1.9-1.4-3.4zm3.8 0h2.3c-.2 2-1.6 3.5-3.4 4 .6-1 1-2.4 1.1-4z"/></svg>
          <span>www.yourwebsite.com</span>
        </li>
      </ul>
    </div>
  </section>

  <section class="card card--back" aria-label="Business card back">
    <div class="brand-mark">
      <span class="brand-mark__square"></span>
      <span class="brand-mark__name">Vantro</span>
      <span class="brand-mark__sub">Transportation</span>
    </div>
  </section>
</main>
</body>
</html>
```